RW Framewell Inc Business cards

We need business cards using our existing logo but slightly modified. Right now the logo says RW Loadbearing Masonry. We want to keep the RW part of the design, but replace the Structural Concrete portion with "FRAMEWELL". Please see the attached file.
Ideally this would be a blank template so we can add Different Names, titles, and phone numbers later.
On the one side we want only the logo and on the other side the detail. I'm attaching an example for you to see.
Please reach out with any other questions. Our address and other details will be given out once we find a design we like.

Target Market(s)

Construction Industry

```html
<!DOCTYPE html>
<html lang="en">
<head>
<meta charset="utf-8">
<title>RW Framewell Inc — Business Cards</title>
<link href="https://fonts.googleapis.com/css2?family=Archivo:wght@400;800&display=swap" rel="stylesheet">
<style>
  :root {
    --brand-blue: #1f76c0;
    --brand-grey: #87888b;
    --paper: #ffffff;
    --backdrop: #1c1c1e;
  }
  * { box-sizing: border-box; margin: 0; padding: 0; }
  html, body {
    width: 1200px; height: 1015px; overflow: hidden;
    background: var(--backdrop);
    font-family: "Archivo", Arial, sans-serif;
  }
  .sheet {
    width: 1200px; height: 1015px;
    display: flex; flex-direction: column; align-items: center; justify-content: center;
    gap: 56px;
  }
  .card {
    position: relative;
    width: 760px; height: 434px;
    overflow: hidden;
  }
  .card--front {
    background: var(--brand-blue);
    display: flex; align-items: center; justify-content: center;
  }
  .wordmark {
    font-weight: 800;
    line-height: 1;
    text-align: center;
    text-transform: uppercase;
  }
  .wordmark__initials { display: block; font-size: 150px; letter-spacing: 4px; }
  .wordmark__name { display: block; font-size: 44px; letter-spacing: 6px; margin-top: 6px; }
  .card--front .wordmark { color: var(--paper); }

  .card--back { background: var(--paper); }
  .card__wave { position: absolute; inset: 0; width: 100%; height: 100%; }
  .card--back .wordmark {
    position: absolute; left: 80px; top: 70px;
    color: var(--brand-blue);
  }
  .card--back .wordmark__initials { font-size: 120px; }
  .card--back .wordmark__name { font-size: 34px; letter-spacing: 5px; }

  .details {
    position: absolute; right: 44px; top: 196px;
    color: var(--paper);
    text-align: right;
  }
  .details__name {
    font-weight: 800; font-size: 27px; letter-spacing: 1px; text-transform: uppercase;
  }
  .details__title { font-weight: 400; font-size: 18px; margin-top: 2px; }
  .details__contacts { list-style: none; margin-top: 20px; }
  .details__contacts li {
    display: flex; align-items: center; justify-content: flex-end; gap: 10px;
    font-size: 19px; line-height: 1.45;
  }
  .details__icon { width: 18px; height: 18px; flex: none; }
</style>
</head>
<body>
<main class="sheet">
  <section class="card card--front" aria-label="Business card front">
    <p class="wordmark">
      <span class="wordmark__initials">RW</span>
      <span class="wordmark__name">Framewell</span>
    </p>
  </section>

  <section class="card card--back" aria-label="Business card back">
    <svg class="card__wave" viewBox="0 0 760 434" preserveAspectRatio="none" aria-hidden="true">
      <path d="M0 372 C170 372 250 350 350 250 C450 150 520 100 690 92" fill="none" stroke="#87888b" stroke-width="9"/>
      <path d="M0 392 C180 392 270 370 370 270 C470 170 540 120 720 112" fill="none" stroke="#1f76c0" stroke-width="5"/>
      <path d="M0 434 L0 410 C190 410 285 388 385 288 C485 188 560 132 760 126 L760 434 Z" fill="#1f76c0"/>
    </svg>

    <p class="wordmark">
      <span class="wordmark__initials">RW</span>
      <span class="wordmark__name">Framewell</span>
    </p>

    <div class="details">
      <p class="details__name">Daniel Harper</p>
      <p class="details__title">Managing Director</p>
      <ul class="details__contacts">
        <li>055-987 654 321
          <svg class="details__icon" viewBox="0 0 24 24" aria-hidden="true"><path fill="#fff" d="M6.6 10.8a15 15 0 0 0 6.6 6.6l2.2-2.2c.3-.3.7-.4 1-.2 1.1.4 2.3.6 3.6.6.6 0 1 .4 1 1V20c0 .6-.4 1-1 1A17 17 0 0 1 3 4c0-.6.4-1 1-1h3.5c.6 0 1 .4 1 1 0 1.3.2 2.5.6 3.6.1.3 0 .7-.2 1z"/></svg>
        </li>
        <li>info@framewellmail.com
          <svg class="details__icon" viewBox="0 0 24 24" aria-hidden="true"><path fill="#fff" d="M2 5h20v14H2z"/><path d="M2 5l10 8 10-8" fill="none" stroke="#1f76c0" stroke-width="2"/></svg>
        </li>
        <li>www.rwframewell.com
          <svg class="details__icon" viewBox="0 0 24 24" aria-hidden="true"><circle cx="12" cy="12" r="10" fill="none" stroke="#fff" stroke-width="2"/><path d="M2 12h20M12 2c3 3 3 17 0 20M12 2c-3 3-3 17 0 20" fill="none" stroke="#fff" stroke-width="1.6"/></svg>
        </li>
      </ul>
    </div>
  </section>
</main>
</body>
</html>
```